One pager digital ad-Corporate travel Manager

I need a design that is smooth, and business like. I don’t like basic generic designs that I can make my self. I’m looking for a sharp clean ad that clearly was made by a great designer. I need some bullet points in and the add to be clean. Here is a list of some content from our content writers. You can arrange and play with the words a bit.

*Budget*- having a travel management service will ensure that your company sticks to a budget which will help PROTECT your bottom line. Travel expenses often CAN BE COSTLY and having a SAVVY corporate travel manager handle YOUR TRAVEL ARRANGEMENTS will make sure that the travel expenses are kept under control.
*Efficiency- time *is money. Have your staff focus on their core business and have the corporate travel manager handle all the logistics for their travel including airfare, hotel cars and events TO MAXIMIZE EFFICIENCY AND KEEP YOUR STAFF FOCUSED ON YOUR CORE BUSINESS

*unforeseen circumstances* – the corporate travel manager handleS any cancellations, missed flights, canceled flights. Quick rebooking, and repositioning, and dealing with getting credits and reimbursement is extremely difficult and time-consuming. The corporate travel manager handles all of that SO YOU CAN CONTINUE ON SCHEDULE WITHOUT SPENDING HOURS REBOOKING AND GETTING CREDIT

Efficient and organized business travel management-help reduce travel expenses, streamline expense reports, optimize booking processes, and make managing the corporate travel experience way easier for all stakeholders involved.

Travel Support

Report on travel spend: In order to optimize their budgets, businesses need to know which departments are spending what on travel. Agencies can report on spend for all stakeholders by team, department, or project, and help you accurately track all your travel expenses.

Maintain compliance: Every company has some sort of rules that make up their travel policy. An agency can enforce these guidelines when booking.

Velnor Trips is a global leader in business travel management services. We drive savings, efficiency and safety to businesses and their travelers all around the world.

If you are looking for a tailored travel management solution, delivering customer service excellence, and a demonstrable return on investment, then you’ve come to the right place

Corporate travel policy compliance
Travel management reports
Meetings and event management
Travel program management
Dedicated travel counselor teams

By listening to your needs and focusing on your goals we can help your company design a global corporate travel service program that controls costs, improves traveler satisfaction and fits your corporate culture.

Our qualified business travel agents and cutting-edge technology deliver solutions that provide the best travel arrangements and travel policy adherence in the business. From CEO to support staff, our services can help make corporate travel a more efficient and enjoyable experience for everyone involved.

With so much involved in travel – from booking and expenses to meetings and strategy – you need the backing of a proven leader…
Velnor Trips, We’re your corporate travel partner to help you manage it all.

```html
<!DOCTYPE html>
<html lang="en">
<head>
<meta charset="utf-8">
<title>Velnor Trips – Travel Management Service</title>
<link href="https://fonts.googleapis.com/css2?family=Poppins:wght@300;400;500;600;700&display=swap" rel="stylesheet">
<style>
  :root{
    --navy:#0b1a3a;
    --ice:#d3ecf7;
    --ice-deep:#b9dff0;
    --ink:#1c2233;
    --white:#ffffff;
    --photo-a:#c9d3de;
    --photo-b:#2c3f66;
  }
  *{box-sizing:border-box;margin:0;padding:0}
  html,body{width:872px;height:1200px;overflow:hidden;background:#ffffff}
  body{font-family:"Poppins",sans-serif;color:var(--ink)}
  .flyer{position:relative;width:872px;height:1200px;background:var(--white);overflow:hidden}
  .hero{position:absolute;left:0;top:0}
  .brand{position:absolute;left:20px;width:400px;top:150px;text-align:center}
  .brand-mark{display:block;margin:0 auto 22px;width:56px;height:56px;border:2px solid var(--ice);border-radius:50%}
  .brand-name{color:var(--white);font-weight:300;font-size:30px;letter-spacing:4px;text-transform:uppercase}
  .page-title{position:absolute;left:53px;top:348px;font-weight:700;font-size:22px;color:var(--navy);letter-spacing:.2px}

  .section-head{position:absolute;left:40px;height:35px}
  .section-head svg{position:absolute;left:0;top:0}
  .section-head h2{position:absolute;left:72px;color:var(--white);font-weight:500;font-size:19px;line-height:1.1;white-space:nowrap}
  .body-copy{position:absolute;font-size:12.2px;line-height:15.6px;color:var(--ink);font-weight:400}

  .why{position:absolute;left:436px;top:398px;width:395px;height:464px;background:var(--navy)}
  .why svg{position:absolute;left:0;top:0}
  .why h2{position:absolute;left:36px;top:6px;width:324px;text-align:center;font-size:17.5px;font-weight:700;color:var(--navy)}
  .why p{position:absolute;left:36px;top:66px;width:335px;color:var(--white);font-size:12.1px;line-height:21.7px}

  .features{position:absolute;left:53px;top:1025px;width:778px;height:101px;background:var(--navy)}
  .feature{position:absolute;top:-8px;height:60px;background:var(--ice);border-radius:3px;display:flex;align-items:center;padding-left:18px;font-size:11.6px;font-weight:600;line-height:14.5px;color:var(--navy);text-transform:uppercase}
  .feature-icon{position:absolute;top:9px;width:30px;height:30px;border-radius:50%;background:var(--white);border:2px solid var(--navy)}
  .tagline{position:absolute;left:0;right:0;top:62px;text-align:center;color:var(--white);font-weight:600;font-size:17px}

  .footer{position:absolute;left:0;top:1150px;width:872px;height:50px}
  .footer-band{position:absolute;left:0;top:0}
  .contact{position:absolute;display:flex;align-items:center;gap:8px;font-size:12px;color:var(--navy);line-height:14px;white-space:nowrap}
  .contact-icon{flex:none;display:block}
  .contact.phone{left:52px;top:14px;color:var(--white);font-weight:700;font-size:16.5px;line-height:20px}
</style>
</head>
<body>
<main class="flyer">

  <svg class="hero" width="872" height="392" viewBox="0 0 872 392">
    <defs>
      <linearGradient id="photoTone" x1="0" y1="0" x2="1" y2="1">
        <stop offset="0" stop-color="var(--photo-a)"/>
        <stop offset="0.55" stop-color="#8496b3"/>
        <stop offset="1" stop-color="var(--photo-b)"/>
      </linearGradient>
    </defs>
    <rect x="0" y="336" width="872" height="56" fill="var(--ice)"/>
    <rect x="0" y="0" width="872" height="336" fill="var(--navy)"/>
    <polygon points="486,0 872,0 872,378 497,378 395,183" fill="var(--ice-deep)"/>
    <polygon points="497,0 872,0 872,378 508,378 407,183" fill="url(#photoTone)" role="img" aria-label="Photo of business travellers in suits walking through an airport with rolling luggage"/>
  </svg>

  <div class="brand">
    <span class="brand-mark"></span>
    <div class="brand-name">Velnor Trips</div>
  </div>

  <h1 class="page-title">TRAVEL MANAGEMENT SERVICE</h1>

  <div class="section-head" style="top:402px">
    <svg width="320" height="40" viewBox="0 0 320 40">
      <polygon points="36,2 292,2 310,38 36,38" fill="var(--navy)"/>
      <line x1="298" y1="2" x2="316" y2="38" stroke="var(--navy)" stroke-width="2"/>
      <circle cx="36" cy="20" r="23" fill="var(--white)" stroke="var(--navy)" stroke-width="2.5"/>
      <circle cx="36" cy="20" r="17" fill="var(--ice)"/>
      <text x="36" y="25" text-anchor="middle" font-family="Poppins,sans-serif" font-size="14" font-weight="600" fill="var(--navy)">$</text>
    </svg>
    <h2 style="top:9px">UNPARALLED SERVICE</h2>
  </div>
  <p class="body-copy" style="left:58px;top:455px;width:360px">Velnor Trips is famous for our concierge style approach to travel. From detailed planning, to commercial or private air travel, transportation, including car rentals, chauffers, busses for larger groups, hotels, all styles of lodging accomodations, special event planning and more, Velnor Trips is like having your own personal or corporate travel butler.</p>

  <div class="section-head" style="top:576px">
    <svg width="320" height="40" viewBox="0 0 320 40">
      <polygon points="36,2 255,2 273,38 36,38" fill="var(--navy)"/>
      <line x1="261" y1="2" x2="279" y2="38" stroke="var(--navy)" stroke-width="2"/>
      <circle cx="36" cy="20" r="23" fill="var(--white)" stroke="var(--navy)" stroke-width="2.5"/>
      <circle cx="36" cy="20" r="17" fill="var(--ice)"/>
      <circle cx="36" cy="20" r="9" fill="none" stroke="var(--navy)" stroke-width="1.8"/>
      <path d="M36 14 V20 H41" fill="none" stroke="var(--navy)" stroke-width="1.8"/>
    </svg>
    <h2 style="top:9px">EFFICIENCY- TIME</h2>
  </div>
  <p class="body-copy" style="left:55px;top:627px;width:360px">Time is your most valuable tool! Our goal at Velnor Trips is to have your employees’ complete focus be on your core business, while having us handle all the logistics for their travel. One of the most appreciated services we offer is the management of travel headaches. Unforeseen circumstances such as cancellations, missed flights, cancelled flights, last minute bookings or changed plans, can take hours to rectify. Velnor Trips handles all of these tedious repositionings expeditiously, saving your employees precious time. Give your company a competitive edge by having Velnor Trips handle your team’s travel arrangements.</p>

  <div class="section-head" style="top:842px;height:48px">
    <svg width="320" height="50" viewBox="0 0 320 50">
      <polygon points="36,2 282,2 300,48 36,48" fill="var(--navy)"/>
      <line x1="288" y1="2" x2="306" y2="48" stroke="var(--navy)" stroke-width="2"/>
      <circle cx="36" cy="25" r="25" fill="var(--white)" stroke="var(--navy)" stroke-width="2.5"/>
      <circle cx="36" cy="25" r="19" fill="var(--ice)"/>
      <rect x="27" y="19" width="18" height="12" rx="1.5" fill="none" stroke="var(--navy)" stroke-width="1.8"/>
      <line x1="24" y1="33" x2="48" y2="33" stroke="var(--navy)" stroke-width="1.8"/>
    </svg>
    <h2 style="top:4px;left:73px">BUDGET AND TRAVEL<br>&nbsp;SPEND REPORTING</h2>
  </div>
  <p class="body-copy" style="left:53px;top:901px;width:782px">Having a travel management service will ensure that your company enforces corporate compliance and maintains control over travel decisions. This ensures that your employees stick to your budget, which in turn will protect your bottom line. Travel expenses can be costly. Having a savvy and experienced corporate travel manager who can access deep discounts not available to the public will ensure your travel is booked across the board at the lowest prices expenses are kept under control. Travel reporting is critical to optimizing budgets, streamlining expense reports, and recognizing key trends. Velnor-Trips customizes travel spend reports, by team, project, department etc, so companies can accurately track travel expenses, and make critical decisions based on the spend.</p>

  <section class="why">
    <svg width="395" height="44" viewBox="0 0 395 44">
      <polygon points="34,0 362,0 346,40 50,40" fill="var(--ice)"/>
    </svg>
    <h2>WHY CHOOSE VELNOR TRIPS?</h2>
    <p>Velnor Trips is a global leader in business travel management services. We drive savings, efficiency, and unparalleled service to businesses and their travelers all around the world. If you are looking for a tailored travel managed solution focused on offering white glove service and fulfilling your individual preferences, while delivering customer excellence, you’ve come to the right place. At Velnor Trips, our mission is to have you focus on your day to day business while we handle all of the logistics and details for the most successful all encompassing travel experience. From emergency passport arrangements to last minute cancellations, re-bookings, and other intricate travel challenges, Velnor Trips is well versed in handling the routine array of travel services, as well as solving any travel related issue that might arise.</p>
  </section>

  <section class="features">
    <div class="feature-icon" style="left:3px"></div>
    <div class="feature" style="left:21px;width:121px">White glove<br>service</div>
    <div class="feature-icon" style="left:155px"></div>
    <div class="feature" style="left:174px;width:135px">Corporate<br>travel policy<br>compliance</div>
    <div class="feature-icon" style="left:321px"></div>
    <div class="feature" style="left:338px;width:128px;padding-left:26px">Streamlined<br>expense<br>reports</div>
    <div class="feature-icon" style="left:475px"></div>
    <div class="feature" style="left:495px;width:128px">Unparalleled<br>savings</div>
    <div class="feature-icon" style="left:632px"></div>
    <div class="feature" style="left:652px;width:128px">Full service<br>travel<br>management</div>
    <p class="tagline">Velnor Trips, We’re your corporate travel partner to help you manage it all.</p>
  </section>

  <footer class="footer">
    <svg class="footer-band" width="872" height="50" viewBox="0 0 872 50">
      <rect x="0" y="0" width="872" height="50" fill="var(--ice)"/>
      <rect x="0" y="45" width="872" height="5" fill="var(--navy)"/>
      <polygon points="0,0 212,0 238,50 0,50" fill="var(--navy)"/>
      <line x1="220" y1="0" x2="246" y2="50" stroke="var(--navy)" stroke-width="3"/>
    </svg>
    <div class="contact phone">
      <svg class="contact-icon" width="16" height="16" viewBox="0 0 24 24"><path d="M6.6 10.8a15 15 0 0 0 6.6 6.6l2.2-2.2a1 1 0 0 1 1-.25 11.4 11.4 0 0 0 3.6.57 1 1 0 0 1 1 1V20a1 1 0 0 1-1 1A17 17 0 0 1 3 4a1 1 0 0 1 1-1h3.5a1 1 0 0 1 1 1c0 1.25.2 2.45.57 3.57a1 1 0 0 1-.25 1z" fill="#fff"/></svg>
      <span>646-318-2075</span>
    </div>
    <div class="contact" style="left:288px;top:7px">
      <svg class="contact-icon" width="14" height="14" viewBox="0 0 24 24"><rect x="2" y="5" width="20" height="14" rx="2" fill="none" stroke="var(--navy)" stroke-width="2"/><path d="M2 6l10 7 10-7" fill="none" stroke="var(--navy)" stroke-width="2"/></svg>
      <span>info@velnor-trips.com</span>
    </div>
    <div class="contact" style="left:446px;top:6px">
      <svg class="contact-icon" width="14" height="16" viewBox="0 0 24 24"><path d="M12 2a7 7 0 0 0-7 7c0 5 7 13 7 13s7-8 7-13a7 7 0 0 0-7-7z" fill="none" stroke="var(--navy)" stroke-width="2"/><circle cx="12" cy="9" r="2.5" fill="var(--navy)"/></svg>
      <span>86 Harlow Street suite 210<br>Brookfield, NY 10920</span>
    </div>
    <div class="contact" style="left:686px;top:8px">
      <svg class="contact-icon" width="15" height="15" viewBox="0 0 24 24"><circle cx="12" cy="12" r="10" fill="none" stroke="var(--navy)" stroke-width="2"/><path d="M2 12h20M12 2c3 3 3 17 0 20M12 2c-3 3-3 17 0 20" fill="none" stroke="var(--navy)" stroke-width="1.6"/></svg>
      <span>Velnor-Trips.com</span>
    </div>
  </footer>

</main>
</body>
</html>
```